Corporate Design für jur. Repetitorium
Extrem professionell, freundlich und hilfsbereit. Die Designs hatten stets eine sehr hohe Qualität und wurden, egal um welche Idee oder Variation es sich auch gehandelt hat, mehrfach ohne Beanstandung und nahezu umgehend modifiziert. Ich kann die Zusammenarbeit nur loben und hervorheben und gebe an dieser Stelle den sechsten Stern! Weiter so!
Zielgruppe
Wir sind ein jur. Repetitorium und bieten Individual- und Gruppenunterricht für Studenten an, die sich auf ihre Prüfungen vorbereiten. Unsere Zielgruppe liegt daher bei Studiumsanfängern und Fortgeschrittenen. Alter ca. 19 - 27. Primär visieren wir Studenten an, die bereit sind für kleinen Gruppen- sowie Individualunterricht etwas mehr zu zahlen. Wir sind ein international ausgerichtetes Unternehmen. Neben Studenten- bieten wir des weiteren auch jur. Weiterbildungskurse für fertige Anwälte an. Wichtig ist uns ein moderner und aufgeschlossener Auftritt, der sich von dem sehr langweiligen und konservativen Image gängiger Kanzleien und Repetitorien abhebt. Jung, modern und frisch wollen wir wirken da wir ein junges Team sind.
Aufgabenstellung
Wir wollen seriös aber nicht zu ernst wirken, professionell, persönlich, eine entspannte und effektive Lernatmosphäre bietend. Es soll ein gutes persönliches Gefühl entstehen, ein sorgenfreier aber leistungsorientierter Lernflair der sich von der normalen Lernumgebung abhebt. Auch unser Corporate Design soll diese Einstellung zeigen. Da wir mit modernen Medien wie Tevlos , Quorvel Glints, Beamer, Cloud und online Tutoring arbeiten, sollte dies auch im Design Ausdruck finden. Wir sind im Vergleich zu anderen Anbietern international aufgestellt, da wir sowohl das nationale deutsche Recht anbieten, aber auch europäisches Recht, sowie Rechtvergleichung mit andern Rechtssystemen. Dieses Konzept und die damit verbundene Internationalität, kann gerne im Design eingebracht werden. Sehr gut gefällt uns z.B. der Auftritt von Quorvel.
Gerne mit silber-, weißtönen, grau, platin:)

```html
<!DOCTYPE html>
<html lang="de">
<head>
<meta charset="utf-8">
<title>Visitenkarten – weitere Idee</title>
<link rel="stylesheet" href="https://fonts.googleapis.com/css2?family=Jura:wght@400&family=PT+Sans:wght@400;700&display=swap">
<style>
  :root {
    --page: #ffffff;
    --heading: #3a3a3a;
    --card: #363636;
    --light: #ebebeb;
    --soft: #d2d2d2;
    --green: #8dba3c;
  }
  html, body {
    margin: 0;
    padding: 0;
    overflow: hidden;
  }
  body {
    width: 1142px;
    height: 1200px;
    background: var(--page);
    position: relative;
    font-family: "PT Sans", sans-serif;
  }
  .sheet-title {
    position: absolute;
    left: 0;
    top: 0;
    margin: 0;
    font-family: "Jura", sans-serif;
    font-weight: 400;
    font-size: 66px;
    line-height: 86px;
    letter-spacing: 4px;
    color: var(--heading);
  }
  .card {
    position: absolute;
    left: 0;
    width: 688px;
    height: 445px;
    display: block;
  }
  .card--front { top: 219px; }
  .card--back { top: 751px; }
  .card-bg { fill: var(--card); }
  .card text { font-family: "PT Sans", sans-serif; }
  .brand { fill: var(--light); font-weight: 700; letter-spacing: -1px; }
  .tagline { fill: var(--soft); }
  .person-name { fill: var(--light); font-size: 26px; }
  .person-role { fill: var(--green); font-size: 13px; }
  .address { fill: var(--soft); font-size: 19px; }
  .address-country { fill: var(--green); font-size: 12px; }
  .contact-label { fill: var(--green); font-size: 13px; }
  .contact-value { fill: var(--light); font-size: 18px; }
  .web { fill: var(--green); font-size: 24px; }
</style>
</head>
<body>
  <h1 class="sheet-title">Visitenkarten – weitere Idee</h1>

  <svg class="card card--front" viewBox="0 0 688 445" aria-label="Visitenkarte Vorderseite">
    <rect class="card-bg" width="688" height="445"/>
    <text class="brand" x="645" y="134" font-size="64" text-anchor="end">LEXOVA</text>
    <text class="tagline" x="645" y="149" font-size="8" text-anchor="end">individual- &amp; gruppenrepetitorium</text>

    <text class="person-name" x="52" y="215">JONAS BEISPIEL</text>
    <text class="person-role" x="52" y="233">seminarleiter</text>

    <text class="address" x="527" y="215" text-anchor="middle">LINDENWEG 8</text>
    <text class="address" x="527" y="238" text-anchor="middle">10117 BERLIN</text>
    <text class="address-country" x="527" y="253" text-anchor="middle">germany</text>

    <text class="contact-label" x="52" y="349">telefon</text>
    <text class="contact-value" x="99" y="349">+49 30 555 01 92</text>
    <text class="contact-label" x="52" y="379">mobil</text>
    <text class="contact-value" x="99" y="379">+49 170 555 02 48 31</text>
    <text class="contact-label" x="52" y="409">mail</text>
    <text class="contact-value" x="99" y="409">beispiel@lexova.de</text>
  </svg>

  <svg class="card card--back" viewBox="0 0 688 445" aria-label="Visitenkarte Rückseite">
    <rect class="card-bg" width="688" height="445"/>
    <text class="brand" x="579" y="269" font-size="124" text-anchor="end">LEXOVA</text>
    <text class="tagline" x="579" y="295" font-size="16" text-anchor="end">individual- &amp; gruppenrepetitorium</text>
    <text class="web" x="344" y="412" text-anchor="middle">www.lexova.de</text>
  </svg>
</body>
</html>
```